Clearing Your Slate - Banner Ad for TH Website

I need a banner ad for a book I'm selling.

The book is about Clearing Your Slate, that is a County Court Judgment, from a credit report.

I have two websites. I want the banner ad to appear on
www.thorncaldwell.co.uk

It will then link to the new site: https://debtslatecleaner.co.uk/

The first site already has a lot of traffic from visitors wanting to remove a CCJ. The purpose of that first site was originally for visitors to become clients of the law firm. However, most visitors can't afford legal advice and so I'd like to offer them the book instead.

I would like to see designs that use the colour green. The final design should communicate financial freedom, simplicity and trustworthiness.

Target Market(s)

Individuals who have discovered a CCJ on their credit report

Industry/Entity Type

Law

Font styles to use
Sans Serif

Colors
0054AA
0677BA
7BADD7
CADEEF
E8F1F8
0094D4
00A9DD
6FCCEA
C7EBF8
E9F6FB
00AB8E
00BBA5
67D7C9
C6EFE9
E9F9F6

Requirements
Must have
• Must fit at the end of a blog article, such as this one https://www.thorncaldwell.co.uk/ccj-wrong-address/

```html
<!DOCTYPE html>
<html lang="en">
<head>
<meta charset="UTF-8">
<title>Clearing Your Slate – Banner</title>
<link href="https://fonts.googleapis.com/css2?family=Montserrat:wght@700;800&display=swap" rel="stylesheet">
<style>
  :root {
    --page-bg: #d9d9d9;
    --green-main: #45a447;
    --green-deep: #3d9a40;
    --green-light: #c9fba8;
    --stripe-gold: #ecce7c;
    --white: #ffffff;
    --cta-red: #ee2a2a;
    --product-tone-a: #ffffff;
    --product-tone-b: #e6e6e6;
  }
  * { margin: 0; padding: 0; box-sizing: border-box; }
  html, body {
    width: 1200px; height: 800px; overflow: hidden;
    background: var(--page-bg);
    font-family: "Montserrat", sans-serif;
  }
  .banner {
    position: absolute;
    left: 20px; top: 161px;
    width: 1160px; height: 478px;
    overflow: hidden;
    background: var(--green-light);
  }
  .banner-shapes { position: absolute; inset: 0; }
  .banner-frame {
    position: absolute;
    left: 15px; top: 16px; right: 15px; bottom: 16px;
    border: 3px solid var(--white);
    pointer-events: none;
  }
  .pitch {
    position: absolute;
    left: 40px; top: 40px; width: 580px;
    text-align: center;
    color: var(--white);
    text-shadow: 2px 3px 0 rgba(0,0,0,0.12);
  }
  .pitch-lead { font-weight: 800; font-size: 54px; line-height: 1; }
  .pitch-big { font-weight: 800; font-size: 104px; line-height: 0.92; letter-spacing: -1px; }
  .pitch-small { font-size: 48px; font-weight: 800; margin-right: 6px; }
  .pitch-sub {
    margin-top: 28px;
    font-weight: 700; font-size: 33px; line-height: 1.22;
  }
  .cta {
    display: block;
    margin: 18px auto 0;
    width: 410px; height: 54px;
    border: 3px solid var(--white);
    border-radius: 27px;
    background: var(--cta-red);
    color: var(--white);
    font-weight: 800; font-size: 29px; line-height: 48px;
    text-decoration: none;
    text-shadow: none;
  }
  .product-visual {
    position: absolute;
    left: 632px; top: 37px; width: 464px; height: 405px;
    background: linear-gradient(135deg, var(--product-tone-a) 0%, var(--product-tone-b) 100%);
    border-radius: 6px;
  }
</style>
</head>
<body>
  <section class="banner">
    <svg class="banner-shapes" width="1160" height="478" viewBox="0 0 1160 478" aria-hidden="true">
      <polygon points="0,0 573,0 870,478 0,478" fill="var(--green-main)"/>
      <polygon points="0,300 0,478 290,478" fill="var(--green-deep)"/>
      <polygon points="573,0 660,0 860,300 800,300" fill="var(--stripe-gold)"/>
    </svg>
    <div class="banner-frame"></div>

    <div class="pitch">
      <div class="pitch-lead">Need to</div>
      <div class="pitch-big">Remove</div>
      <div class="pitch-big"><span class="pitch-small">a</span>CCJ?</div>
      <p class="pitch-sub">Find out how with this simple<br>jargon-free guide</p>
      <a class="cta" href="https://debtslatecleaner.co.uk/">Get Your Copy Now</a>
    </div>

    <div class="product-visual" role="img" aria-label="Tablet, phone and paperback showing the book cover of Clearing Your Slate by Nathan Vale, Solicitor"></div>
  </section>
</body>
</html>
```